BildeVOLD buisnesscard

Hey :) I need a modern buisnesscard for my company BildeVOLD
It most have:
Dagligleder og Fotograf: Henrik Audun Strandvik

Mob: +4791264085
Epost: post@bildevold.example
Adresse: Kvernbakken9, 6040 Strandnes

Facbook and instagram logo with text BildeVOLD

BildeVOLD logo

It Company

```html
<!DOCTYPE html>
<html lang="no">
<head>
<meta charset="utf-8">
<title>BildeVOLD business card</title>
<link href="https://fonts.googleapis.com/css2?family=Roboto:wght@400;700&display=swap" rel="stylesheet">
<style>
  :root {
    --backdrop: #463b36;
    --card-black: #1c1c1d;
    --card-edge: #2a2a2b;
    --mark-grey: #8e8e90;
    --text-light: #d6d6d6;
    --text-muted: #a8a8a8;
    --band-mid: #6f6f71;
    --band-light: #a7a8aa;
    --band-text: #2a2a2b;
  }
  * { margin: 0; padding: 0; box-sizing: border-box; }
  html, body {
    width: 1200px; height: 716px; overflow: hidden;
    background: var(--backdrop);
    font-family: "Roboto", Arial, sans-serif;
  }
  .stage {
    position: relative; width: 1200px; height: 716px;
    display: flex; align-items: center; justify-content: center; gap: 60px;
  }
  .card {
    position: relative; width: 520px; height: 300px;
    background: var(--card-black);
    border: 1px solid var(--card-edge);
    overflow: hidden;
  }
  .card-front {
    display: flex; align-items: center; justify-content: center;
  }
  .front-wordmark {
    font-weight: 700; font-size: 54px; color: var(--mark-grey);
    letter-spacing: 1px;
  }
  .card-back .bands { position: absolute; inset: 0; }
  .back-wordmark {
    position: absolute; left: 0; width: 250px; top: 116px;
    text-align: center;
    font-weight: 700; font-size: 34px; color: var(--mark-grey);
  }
  .divider {
    position: absolute; left: 255px; top: 42px; width: 1px; height: 176px;
    background: var(--text-muted);
  }
  .details { position: absolute; left: 278px; top: 70px; color: var(--text-light); }
  .person-name { font-weight: 700; font-size: 17px; }
  .person-title { font-size: 12px; color: var(--text-muted); margin-top: 3px; }
  .contact-list { list-style: none; margin-top: 14px; }
  .contact-list li {
    display: flex; align-items: center; gap: 9px;
    font-size: 13px; line-height: 20px;
  }
  .contact-list svg { width: 12px; height: 12px; flex: none; }
  .social {
    position: absolute; left: 290px; top: 262px;
    display: flex; align-items: center; gap: 8px;
    font-size: 15px; color: var(--band-text);
  }
  .social-square { width: 13px; height: 13px; background: var(--band-text); }
</style>
</head>
<body>
<main class="stage">
  <section class="card card-front" aria-label="Card front">
    <span class="front-wordmark">BildeVOLD</span>
  </section>

  <section class="card card-back" aria-label="Card back">
    <svg class="bands" viewBox="0 0 520 300" aria-hidden="true">
      <polygon points="0,246 242,246 228,262 0,262" fill="var(--band-mid)"/>
      <polygon points="252,246 520,246 520,300 205,300" fill="var(--band-light)"/>
    </svg>
    <span class="back-wordmark">BildeVOLD</span>
    <div class="divider"></div>
    <div class="details">
      <p class="person-name">Henrik Audun Strandvik</p>
      <p class="person-title">Managing Director &amp; Photographer</p>
      <ul class="contact-list">
        <li>
          <svg viewBox="0 0 12 12"><rect x="3" y="0.5" width="6" height="11" rx="1.2" fill="none" stroke="currentColor"/><circle cx="6" cy="9.5" r="0.7" fill="currentColor"/></svg>
          +4791264085
        </li>
        <li>
          <svg viewBox="0 0 12 12"><rect x="0.5" y="2.5" width="11" height="7" fill="none" stroke="currentColor"/><polyline points="0.5,2.5 6,7 11.5,2.5" fill="none" stroke="currentColor"/></svg>
          post@bildevold.example
        </li>
        <li>
          <svg viewBox="0 0 12 12"><path d="M6 11.5 C3 7.5 2 6 2 4.2 A4 4 0 0 1 10 4.2 C10 6 9 7.5 6 11.5Z" fill="currentColor"/><circle cx="6" cy="4.3" r="1.4" fill="var(--card-black)"/></svg>
          Kvernbakken9, 6040 Strandnes
        </li>
      </ul>
    </div>
    <div class="social">
      <span class="social-square"></span>
      <span>/BildeVOLD</span>
    </div>
  </section>
</main>
</body>
</html>
```